Web Design Project - Shipping Industry

Goals and Objectives
The objective of the new website is to create a more modern look and feel. The site will also allow for a more effective means of communicating with members while providing the public with information and developments in the local, regional and international shipping industry.
Scope
The website will highlight the history of the organisation inclusive of text and photographs. It will take visitors through the years from beginning to present. Information on the history of the shipping industry will also be included.
It will feature current articles on the organisation, its members and stakeholders in the shipping industry. Member information as well as pertinent details regarding the organisation’s subsidiaries will be documented for the website.
Information as it relates to shipping statistics, case studies, laws and regulations, international treaties and trade documents, shipping terms, careers in shipping, job opportunities, training opportunities, information for shippers including port listing and trade lanes will be main features of the content for the website.
The Association’s community involvement, industry calendar events and related links relevant industry members will also be featured.
Target Market
• The General Public;
• Members of the organization;
• Shipping Industry Stakeholders (local, regional and international);
• Tertiary students conducting research.
• Potential employees
• Potential Business Partners
Best Practice Bench Marketing
The following websites are being looked at:
• Korvel Quayworks - http://www.korvelquayworks.example/ (preferred look)
• Tessaly Maritime Association - http://www.tma-freight.example/ (like image transition on main page)
• Drovna - http://www.drovna.example (professional look)
• PLW - http://www.pelworth.example (preferred color: blue in logo)
• Quillo - http://www.quillo.example/electronics/tv-video-audio/ (preferred look for links page: image + short text below + visit site link)
Expected Result
• 3 - 5 pages which must include: [1] main page [2] standard page [3] links page

```html
<!DOCTYPE html>
<html lang="en">
<head>
<meta charset="utf-8">
<title>Harbourline Data Services</title>
<link rel="stylesheet" href="https://fonts.googleapis.com/css2?family=Source+Sans+3:ital,wght@0,300;0,400;0,600;0,700;1,400&display=swap">
<style>
:root{
  --navy:#0d2266;
  --navy-deep:#06185a;
  --blue:#1b55c8;
  --link:#1a4fc0;
  --gold:#f0c419;
  --ink:#1a1a1a;
  --text:#333;
  --muted:#8a8a8a;
  --rule:#d6d6d6;
  --page-bg:#e6e6e6;
  --placeholder:#e9ecf2;
}
*{box-sizing:border-box;margin:0;padding:0}
html,body{width:1040px;height:1200px;overflow:hidden;background:#fff}
body{font-family:"Source Sans 3",sans-serif;color:var(--text);position:relative}
.backdrop{position:absolute;left:0;top:0;width:1040px;height:1088px;background:var(--page-bg)}
.page{position:absolute;left:86px;top:0;width:864px;height:1088px;background:#fff;box-shadow:0 0 6px rgba(0,0,0,.18)}
.abs{position:absolute}
a{color:inherit;text-decoration:none}

.account-links{left:741px;top:10px;font-size:12px;color:var(--ink)}
.account-links span{margin:0 6px}
.brand{left:36px;top:50px;font-size:26px;font-weight:600;letter-spacing:9px;color:var(--navy)}
.social{left:570px;top:57px;display:flex;gap:5px}
.social i{display:block;width:12px;height:12px;background:#3a6fb8;border-radius:2px}
.social i:nth-child(2){background:#3b5998}
.social i:nth-child(3){background:#4aa6d8}
.social i:nth-child(4){background:#c9302c}
.search{left:643px;top:52px;width:192px;height:22px;border:1px solid #d3d3d3;font-size:11px;color:#222;padding:4px 9px;display:flex;justify-content:space-between;align-items:center}

.nav{left:35px;top:110px;width:800px;height:36px;border-top:2px solid var(--gold);background:linear-gradient(#2957c9,var(--navy-deep));display:flex;justify-content:space-around;align-items:center;padding:0 10px}
.nav a{color:#fff;font-size:10px;font-weight:700;letter-spacing:.2px}

.hero{left:35px;top:146px;width:800px;height:272px;display:flex}
.hero .photo{flex:1}
.hero .photo.quay{background:linear-gradient(135deg,#8e9aa6,#4b6b92 45%,#b9573a)}
.hero .photo.cranes{background:linear-gradient(160deg,#c7c9c4,#b86a3c 50%,#cf5b2d)}
.caption{left:34px;top:418px;width:801px;height:64px;background:linear-gradient(#2b63d4,#1c4fbf);color:#fff}
.caption h1{position:absolute;left:21px;top:14px;font-size:28px;font-weight:400;letter-spacing:-.3px}
.caption p{position:absolute;left:374px;top:12px;width:400px;font-size:12.5px;line-height:18px}
.more-btn{font-weight:600;margin-left:6px;font-size:11.5px;white-space:nowrap}
.arrow{display:inline-block;vertical-align:-2px;margin-left:4px}

.intro-mark{left:47px;top:508px;width:52px;height:52px;background:var(--placeholder)}
.intro{left:137px;top:518px;width:525px;font-size:14px;line-height:19px;font-weight:300;color:#333}
.intro strong{font-weight:400}

.login{left:698px;top:500px;width:121px}
.login h3{font-size:11px;font-weight:700;color:var(--link)}
.login .field{margin-top:6px;height:22px;border:1px solid #cfcfcf;font-size:11px;color:#222;padding:3px 7px}
.login .field+.field{margin-top:9px}
.login .links{margin-top:7px;font-size:8.5px;font-weight:600;color:var(--ink);padding-left:2px}
.login .links span{margin:0 6px}

.news{left:45px;top:608px;width:250px}
.news h2{font-size:18px;font-weight:700;color:var(--link);margin-bottom:12px}
.news article{margin-bottom:14px}
.news h4{font-size:12px;font-weight:600;color:var(--ink);line-height:16px}
.news time{display:block;font-size:11px;font-style:italic;color:var(--muted);line-height:16px;margin-bottom:3px}
.news p{font-size:10.5px;line-height:16px;color:#222}
.news p a{color:var(--link);font-weight:600}

.feature{left:331px;width:325px;height:100px}
.feature .thumb{position:absolute;left:0;top:0;width:151px;height:97px}
.feature h3{position:absolute;left:164px;top:0;font-size:12px;font-weight:700;color:var(--link)}
.feature p{position:absolute;left:164px;top:21px;width:158px;font-size:8.3px;line-height:12.8px;color:#222}
.feature .learn{position:absolute;left:164px;top:85px;font-size:10px;font-weight:700;color:var(--link)}
.feature.one{top:615px}.feature.two{top:750px}.feature.three{top:883px}
.one .thumb{background:linear-gradient(135deg,#b8916a,#cfc5b2 50%,#7b7d6a)}
.two .thumb{background:linear-gradient(135deg,#4f5f57,#1f7a6a 45%,#b7c0bf)}
.three .thumb{background:linear-gradient(160deg,#8aa0b4,#a06a4a 55%,#e08a2a)}
.divider{left:331px;width:325px;height:1px;background:var(--rule)}

.partners{left:699px;top:615px;width:110px}
.partner{position:absolute;left:0;font-size:12px;font-weight:700;color:var(--navy);display:flex;align-items:center;gap:5px;white-space:nowrap}
.partner i{display:block;width:12px;height:12px;background:var(--gold)}

.footer{left:0;top:1010px;width:864px;height:39px;background:linear-gradient(#2e5fd2,var(--navy-deep) 55%);color:#fff;font-size:9px}
.footer .copy{position:absolute;left:35px;top:15px}
.footer nav{position:absolute;right:45px;top:15px}
.footer nav span{margin:0 10px}
</style>
</head>
<body>
<div class="backdrop"></div>
<div class="page">
  <div class="abs account-links"><a href="#">Register</a><span>|</span><a href="#">Login</a></div>
  <div class="abs brand">KEELWRIGHT</div>
  <div class="abs social" aria-label="Social links"><i></i><i></i><i></i><i></i></div>
  <div class="abs search">Search
    <svg width="13" height="13" viewBox="0 0 13 13"><circle cx="8" cy="5" r="4" fill="none" stroke="#bbb" stroke-width="1.4"/><line x1="5" y1="8" x2="1" y2="12" stroke="#bbb" stroke-width="1.6"/></svg>
  </div>

  <nav class="abs nav">
    <a href="#">HOME</a><a href="#">ABOUT US</a><a href="#">PRODUCTS</a><a href="#">SERVICES</a><a href="#">NEWS</a><a href="#">SUPPORT</a><a href="#">PARTNERS</a><a href="#">CUSTOMERS</a><a href="#">CONTACT</a>
  </nav>

  <div class="abs hero">
    <div class="photo quay" role="img" aria-label="Two engineers in hard hats reviewing a laptop beside stacked shipping containers"></div>
    <div class="photo cranes" role="img" aria-label="Port workers in safety vests walking beneath a container straddle carrier"></div>
  </div>
  <div class="abs caption">
    <h1>Harbourline Data Services</h1>
    <p>Built for operation in a port or agent environment, it is a powerful platform to manage their operations and drive efficiencies <a class="more-btn" href="#">LEARN MORE<svg class="arrow" width="12" height="12" viewBox="0 0 12 12"><circle cx="6" cy="6" r="6" fill="#fff"/><path d="M3 6h5M6 3.5 8.5 6 6 8.5" stroke="#1c4fbf" stroke-width="1.5" fill="none"/></svg></a></p>
  </div>

  <div class="abs intro-mark" role="img" aria-label="Company emblem placeholder"></div>
  <p class="abs intro"><strong>Harbourline Data Services</strong> (KEELWRIGHT), a subsidiary of the Coral Bay Shipping Association, was established in 1981 to provide information technology infrastructure and systems support to the local port community and the wider Caribbean maritime sector.</p>

  <form class="abs login">
    <h3>MEMEBR LOGIN</h3>
    <div class="field">Username</div>
    <div class="field">Password</div>
    <div class="links">Register<span>|</span>Forgot Password?</div>
  </form>

  <section class="abs news">
    <h2>LATEST NEWS</h2>
    <article>
      <h4>HDS Launches Document Management<br>Software</h4>
      <time>March 10, 2012</time>
      <p>Harbourline Data Services Limited (HDS), along with its partner Fernhollow Technologies Incorporated, presented the Ledgerly Enterprise Document Management Software durind... <a href="#">Read more »</a></p>
    </article>
    <article>
      <h4>Business Continuity - Are you prepared ?</h4>
      <time>March 8, 2012</time>
      <p>Business continuity should be the number one priority of every organization, since failure to have a contingency plan has repeatedly... <a href="#">Read more »</a></p>
    </article>
    <article>
      <h4>Marisa Dunmore Returned As Customs Brokers President</h4>
      <time>March 8, 2012</time>
      <p>Business continuity should be the number one priority of every organization, since failure to have a contingency plan has repeatedly... <a href="#">Read more »</a></p>
    </article>
  </section>

  <div class="abs feature one">
    <div class="thumb" role="img" aria-label="Trainer and trainee reviewing plans in a warehouse"></div>
    <h3>TRAINING OPPORTUNITIES</h3>
    <p>Lorem ipsum dolor sit amet, consectetur adipisicing elit, sed do eiusmod tempor incididunt ut labore et dolore magna aliqua. Ut enim ad minim veniam, quis</p>
    <a class="learn" href="#">LEARN MORE<svg class="arrow" width="12" height="12" viewBox="0 0 12 12"><circle cx="6" cy="6" r="6" fill="#1a4fc0"/><path d="M3 6h5M6 3.5 8.5 6 6 8.5" stroke="#fff" stroke-width="1.5" fill="none"/></svg></a>
  </div>
  <div class="abs divider" style="top:728px"></div>
  <div class="abs feature two">
    <div class="thumb" role="img" aria-label="Operator monitoring screens in a port control room"></div>
    <h3>JOB OPPORTUNITIES</h3>
    <p>Lorem ipsum dolor sit amet, consectetur adipisicing elit, sed do eiusmod tempor incididunt ut labore et dolore magna aliqua. Ut enim ad minim veniam, quis</p>
    <a class="learn" href="#">LEARN MORE<svg class="arrow" width="12" height="12" viewBox="0 0 12 12"><circle cx="6" cy="6" r="6" fill="#1a4fc0"/><path d="M3 6h5M6 3.5 8.5 6 6 8.5" stroke="#fff" stroke-width="1.5" fill="none"/></svg></a>
  </div>
  <div class="abs divider" style="top:866px"></div>
  <div class="abs feature three">
    <div class="thumb" role="img" aria-label="Dock workers in safety vests walking along a container quay"></div>
    <h3>CAREERS IN SHIPPING</h3>
    <p>Lorem ipsum dolor sit amet, consectetur adipisicing elit, sed do eiusmod tempor incididunt ut labore et dolore magna aliqua. Ut enim ad minim veniam, quis</p>
    <a class="learn" href="#">LEARN MORE<svg class="arrow" width="12" height="12" viewBox="0 0 12 12"><circle cx="6" cy="6" r="6" fill="#1a4fc0"/><path d="M3 6h5M6 3.5 8.5 6 6 8.5" stroke="#fff" stroke-width="1.5" fill="none"/></svg></a>
  </div>

  <aside class="abs partners">
    <div class="partner" style="top:12px"><i></i>Brinegate Marine</div>
    <div class="partner" style="top:72px"><i></i>Calder Wharves</div>
    <div class="partner" style="top:130px"><i></i>Tollmark Handlers</div>
    <div class="partner" style="top:192px"><i></i>Sandreach Line</div>
    <div class="partner" style="top:245px"><i></i>Vora</div>
    <div class="partner" style="top:308px"><i></i>Keelpath Freight</div>
  </aside>

  <footer class="abs footer">
    <div class="copy">© HARBOURLINE DATA SERVICES | ALL RIGHT RESERVED</div>
    <nav>LEGAL NOTICE<span>|</span>PRIVACY POLICY<span>|</span>CONTACT US</nav>
  </footer>
</div>
</body>
</html>
```